Restaurant Facility Equipment & Store Maintenance/

I need a flyer showing commercial/industrial kitchen equipment photos we work on Hot Equipment & Cold Equipment and offer many services. see attached highlights

```html
<!DOCTYPE html>
<html lang="en">
<head>
<meta charset="utf-8">
<title>Restaurant Facility Equipment &amp; Store Maintenance Flyer</title>
<link rel="stylesheet" href="https://fonts.googleapis.com/css2?family=Source+Sans+3:wght@400;700;900&family=Roboto:wght@400;500&display=swap">
<style>
  :root {
    --page-bg: #c9c7c3;
    --paper: #ffffff;
    --brand-blue: #1a4c9b;
    --brand-navy: #0d2353;
    --ink: #222222;
    --muted: #8a8a8a;
    --rule: #6f8fc4;
  }
  * { box-sizing: border-box; margin: 0; padding: 0; }
  html, body {
    width: 1200px; height: 3000px; overflow: hidden;
    background: var(--page-bg);
  }
  .flyer {
    position: absolute; left: 50px; top: 788px;
    width: 1100px; height: 1423px;
    background: var(--paper); overflow: hidden;
    font-family: "Roboto", Arial, sans-serif; color: var(--ink);
  }
  .hero-photo {
    position: absolute; left: 404px; top: 0; width: 696px; height: 461px;
    background: linear-gradient(90deg, #ffffff 0%, #e4e7ea 22%, #c3c8cc 55%, #9ea5aa 100%);
  }
  .logo {
    position: absolute; left: 53px; top: 50px;
    font-family: "Source Sans 3", Arial, sans-serif; font-weight: 400;
    font-size: 38px; color: var(--muted); letter-spacing: 0.5px;
  }
  .headline {
    position: absolute; left: 52px; top: 108px;
    font-family: "Source Sans 3", Arial, sans-serif; text-transform: uppercase;
    font-size: 60px; line-height: 60px;
  }
  .headline .lead { display: block; color: var(--brand-blue); font-weight: 700; }
  .headline .strong { display: block; color: var(--brand-navy); font-weight: 900; }
  .subtitle {
    position: absolute; left: 55px; top: 362px; width: 560px;
    font-size: 20px; line-height: 24px; color: var(--brand-navy);
  }
  .band-accent {
    position: absolute; left: 145px; top: 461px; width: 808px; height: 9px;
    background: var(--brand-blue);
  }
  .intro-band {
    position: absolute; left: 0; top: 470px; width: 953px; height: 160px;
    background: var(--brand-navy); color: #fff;
    padding: 40px 20px 0 50px; font-size: 19.5px; line-height: 24px;
  }
  .intro-band span { display: block; white-space: nowrap; }
  .services-mark { position: absolute; left: 52px; top: 658px; width: 74px; height: 74px; }
  .services-title {
    position: absolute; left: 89px; top: 945px;
    transform: translate(-50%, -50%) rotate(-90deg);
    font-family: "Source Sans 3", Arial, sans-serif; font-weight: 900;
    font-size: 52px; line-height: 52px; letter-spacing: 2px; color: var(--brand-blue); white-space: nowrap;
  }
  .service-list {
    position: absolute; left: 153px; top: 668px; width: 804px;
    display: grid; grid-template-columns: 375px 382px; column-gap: 50px;
    grid-template-rows: 52px 78px 95px 78px 75px 69px 70px auto;
    grid-auto-flow: column; list-style: none;
  }
  .service-list li {
    display: flex; gap: 16px; padding-top: 20px;
    font-size: 16.5px; line-height: 19px;
    border-bottom: 1.5px dashed var(--rule);
  }
  .service-list li span { white-space: nowrap; }
  .service-list li.no-rule { border-bottom: none; }
  .service-list .col-left { grid-column: 1; }
  .service-list .col-right { grid-column: 2; }
  .tick { flex: 0 0 16px; width: 16px; height: 16px; margin-top: 1px; }
  .phone-bar {
    position: absolute; left: 0; top: 1226px; width: 397px; height: 81px;
    background: var(--brand-blue); color: #fff;
    display: flex; align-items: center; padding-left: 53px; gap: 18px;
    font-family: "Source Sans 3", Arial, sans-serif; font-weight: 700; font-size: 37px;
  }
  .phone-bar svg { width: 54px; height: 54px; }
  .contact-footer {
    position: absolute; left: 0; top: 1307px; width: 1100px; height: 116px;
    background: var(--brand-navy); color: #fff;
    display: flex; align-items: center; font-size: 18.5px; line-height: 22px;
  }
  .contact-item { display: flex; align-items: flex-start; gap: 12px; }
  .contact-item svg { width: 16px; height: 16px; margin-top: 3px; flex: 0 0 16px; }
  .contact-address { margin-left: 64px; width: 364px; }
  .contact-divider { width: 1.5px; height: 36px; background: rgba(255,255,255,0.5); }
  .contact-email { margin: 0 47px 0 40px; }
  .contact-web { margin-left: 26px; }
</style>
</head>
<body>
<main class="flyer">
  <div class="hero-photo" role="img" aria-label="Photo of a stainless steel commercial kitchen with exhaust hood, ranges and combi oven"></div>

  <div class="logo">LOGO HERE</div>
  <h1 class="headline">
    <span class="lead">We handle</span>
    <span class="lead">everything from</span>
    <span class="strong">the front door to</span>
    <span class="strong">the back door</span>
  </h1>
  <p class="subtitle">Installation, Rebuilds, OSHA Inspection, and Preventive Maintenance Services for Denver Metro and Surrounding Areas.</p>

  <div class="band-accent"></div>
  <p class="intro-band"><span>We offer hot and cold equipment repair, cleaning, maintenance, handyman work, drywall, painting,</span><span>door closers, floors, and ceiling tiles. For any need in your restaurant, call us and we will send a</span><span>skilled technician to manage all your commercial andindustrial facility requirements.</span></p>

  <svg class="services-mark" viewBox="0 0 74 74" aria-hidden="true">
    <circle cx="37" cy="37" r="36" fill="#1a4c9b"/>
    <circle cx="37" cy="37" r="28" fill="none" stroke="#fff" stroke-width="2"/>
    <circle cx="37" cy="37" r="17" fill="none" stroke="#fff" stroke-width="5" stroke-dasharray="5 3.9"/>
    <circle cx="37" cy="37" r="13" fill="none" stroke="#fff" stroke-width="2"/>
    <circle cx="37" cy="37" r="6" fill="none" stroke="#fff" stroke-width="2"/>
  </svg>
  <h2 class="services-title">OUR SERVICES</h2>

  <ul class="service-list">
    <li class="col-left"><svg class="tick" viewBox="0 0 16 16"><rect x="1" y="3" width="12" height="12" fill="none" stroke="#1a4c9b" stroke-width="1.6"/><path d="M4 8.5l3 3 8-9" fill="none" stroke="#1a4c9b" stroke-width="2"/></svg><span>KESTA Certified Technicians</span></li>
    <li class="col-left"><svg class="tick" viewBox="0 0 16 16"><rect x="1" y="3" width="12" height="12" fill="none" stroke="#1a4c9b" stroke-width="1.6"/><path d="M4 8.5l3 3 8-9" fill="none" stroke="#1a4c9b" stroke-width="2"/></svg><span>Round-the-clock emergency services</span></li>
    <li class="col-left"><svg class="tick" viewBox="0 0 16 16"><rect x="1" y="3" width="12" height="12" fill="none" stroke="#1a4c9b" stroke-width="1.6"/><path d="M4 8.5l3 3 8-9" fill="none" stroke="#1a4c9b" stroke-width="2"/></svg><span>Customers who subscribe to preventive<br>maintenance services receive a<br>reduced rate on hourly labor charges.</span></li>
    <li class="col-left"><svg class="tick" viewBox="0 0 16 16"><rect x="1" y="3" width="12" height="12" fill="none" stroke="#1a4c9b" stroke-width="1.6"/><path d="M4 8.5l3 3 8-9" fill="none" stroke="#1a4c9b" stroke-width="2"/></svg><span>Original equipment manufacturer<br>(OEM) parts</span></li>
    <li class="col-left"><svg class="tick" viewBox="0 0 16 16"><rect x="1" y="3" width="12" height="12" fill="none" stroke="#1a4c9b" stroke-width="1.6"/><path d="M4 8.5l3 3 8-9" fill="none" stroke="#1a4c9b" stroke-width="2"/></svg><span>30-day warranty on all OEM parts installed</span></li>
    <li class="col-left"><svg class="tick" viewBox="0 0 16 16"><rect x="1" y="3" width="12" height="12" fill="none" stroke="#1a4c9b" stroke-width="1.6"/><path d="M4 8.5l3 3 8-9" fill="none" stroke="#1a4c9b" stroke-width="2"/></svg><span>Equipment Cleaning &amp; Rebuilds</span></li>
    <li class="col-left no-rule"><svg class="tick" viewBox="0 0 16 16"><rect x="1" y="3" width="12" height="12" fill="none" stroke="#1a4c9b" stroke-width="1.6"/><path d="M4 8.5l3 3 8-9" fill="none" stroke="#1a4c9b" stroke-width="2"/></svg><span>Hot &amp; Cold Equipment</span></li>

    <li class="col-right"><svg class="tick" viewBox="0 0 16 16"><rect x="1" y="3" width="12" height="12" fill="none" stroke="#1a4c9b" stroke-width="1.6"/><path d="M4 8.5l3 3 8-9" fill="none" stroke="#1a4c9b" stroke-width="2"/></svg><span>Used equipment available for purchase or rental</span></li>
    <li class="col-right"><svg class="tick" viewBox="0 0 16 16"><rect x="1" y="3" width="12" height="12" fill="none" stroke="#1a4c9b" stroke-width="1.6"/><path d="M4 8.5l3 3 8-9" fill="none" stroke="#1a4c9b" stroke-width="2"/></svg><span>Specialized Programs for Preventive<br>Maintenance of Equipment</span></li>
    <li class="col-right"><svg class="tick" viewBox="0 0 16 16"><rect x="1" y="3" width="12" height="12" fill="none" stroke="#1a4c9b" stroke-width="1.6"/><path d="M4 8.5l3 3 8-9" fill="none" stroke="#1a4c9b" stroke-width="2"/></svg><span>Comprehensive licensed electrical contractor services<br>for both interior and exterior projects, including<br>lighting system upgrades.</span></li>
    <li class="col-right"><svg class="tick" viewBox="0 0 16 16"><rect x="1" y="3" width="12" height="12" fill="none" stroke="#1a4c9b" stroke-width="1.6"/><path d="M4 8.5l3 3 8-9" fill="none" stroke="#1a4c9b" stroke-width="2"/></svg><span>Repair or replace restaurant furniture</span></li>
    <li class="col-right"><svg class="tick" viewBox="0 0 16 16"><rect x="1" y="3" width="12" height="12" fill="none" stroke="#1a4c9b" stroke-width="1.6"/><path d="M4 8.5l3 3 8-9" fill="none" stroke="#1a4c9b" stroke-width="2"/></svg><span>Building Graffiti Removal Services</span></li>
    <li class="col-right"><svg class="tick" viewBox="0 0 16 16"><rect x="1" y="3" width="12" height="12" fill="none" stroke="#1a4c9b" stroke-width="1.6"/><path d="M4 8.5l3 3 8-9" fill="none" stroke="#1a4c9b" stroke-width="2"/></svg><span>Installation and Repair of Restaurant Equipment</span></li>
    <li class="col-right"><svg class="tick" viewBox="0 0 16 16"><rect x="1" y="3" width="12" height="12" fill="none" stroke="#1a4c9b" stroke-width="1.6"/><path d="M4 8.5l3 3 8-9" fill="none" stroke="#1a4c9b" stroke-width="2"/></svg><span>Food Service Trucks</span></li>
    <li class="col-right no-rule"><svg class="tick" viewBox="0 0 16 16"><rect x="1" y="3" width="12" height="12" fill="none" stroke="#1a4c9b" stroke-width="1.6"/><path d="M4 8.5l3 3 8-9" fill="none" stroke="#1a4c9b" stroke-width="2"/></svg><span>We repair floors, walls, counters, décor, signage,<br>parking lots, dumpsters, and more. If you have it,<br>we probably fix it.</span></li>
  </ul>

  <div class="phone-bar">
    <svg viewBox="0 0 54 54" aria-hidden="true">
      <circle cx="27" cy="27" r="27" fill="#fff"/>
      <path d="M19 14c1.5-1 3-.6 3.8.8l2.4 4.2c.7 1.2.3 2.5-.8 3.2l-1.6 1c1 2.7 3.3 5.3 6 6.6l1.1-1.5c.8-1 2.1-1.3 3.2-.6l4.1 2.5c1.3.8 1.6 2.4.7 3.7l-1.4 2c-1.2 1.7-3.3 2.3-5.3 1.6-7.1-2.6-12.5-8.3-14.6-15.5-.6-2 .2-4 1.9-5.1z" fill="#1a4c9b"/>
    </svg>
    <span>111(999)5555</span>
  </div>

  <footer class="contact-footer">
    <div class="contact-item contact-address">
      <svg viewBox="0 0 16 16" aria-hidden="true"><path d="M8 1a5 5 0 0 0-5 5c0 3.5 5 9 5 9s5-5.5 5-9a5 5 0 0 0-5-5zm0 7a2 2 0 1 1 0-4 2 2 0 0 1 0 4z" fill="#fff"/></svg>
      <span>Lorem ipsum dolor sit amet,consectetur adipiscing elit,</span>
    </div>
    <div class="contact-divider"></div>
    <div class="contact-item contact-email">
      <svg viewBox="0 0 16 16" aria-hidden="true"><rect x="1" y="3.5" width="14" height="9" fill="none" stroke="#fff" stroke-width="1.5"/><path d="M1 4l7 5 7-5" fill="none" stroke="#fff" stroke-width="1.5"/></svg>
      <span>info@yourcompany.com</span>
    </div>
    <div class="contact-divider"></div>
    <div class="contact-item contact-web">
      <svg viewBox="0 0 16 16" aria-hidden="true"><circle cx="8" cy="8" r="6.5" fill="none" stroke="#fff" stroke-width="1.4"/><ellipse cx="8" cy="8" rx="2.8" ry="6.5" fill="none" stroke="#fff" stroke-width="1.2"/><path d="M1.5 8h13M2.5 4.8h11M2.5 11.2h11" stroke="#fff" stroke-width="1.1"/></svg>
      <span>www.yourcompany.com</span>
    </div>
  </footer>
</main>
</body>
</html>
```